Creative, fresh business card design for Ripplecraft Facades

We need a fresh, creative business card design for Ripplecraft Facades. We are the manufacturer of Ripplecraft Facades in Australia. Wall panels are 2400 x 1200mm panels made from MDF and feature 3D patterns on the face of the panel. The colours to be used are green, silver/grey and white RGB
Red 187
Green 207
Blue 65.

An idea is to possibly use a watermark of one of our designs as a background (like on the "Grids" design on the left hand side of page 2 of our brochure).

Target Market(s)

Interior designers, architects, builders and home renovators

Industry/Entity Type

Business

Contact Information for Business Card

Details to go on the card are:
Our logo (attached),
Slogan: "Decorative panels for interiors and exteriors",
Contact name,
Position,
Mobile phone number,
Business address,
Business phone,
Business fax,
Website and
Email address.

I have attached a few images of our panels and our brochure for reference.

The colours of the business card should feature our logo colours which are: RGB
Red 187
Green 207
Blue 65

Requirements
Must have
• Very modern fonts and design. Some of the designs shown especially the "Prisms" design which is a popular design.
Nice to have
• Creative but simple design. Very contemporary.
Should not have
• Anything ornate or old fashioned.

```html
<!DOCTYPE html>
<html lang="en">
<head>
<meta charset="utf-8">
<title>Ripplecraft Facades — Business Card</title>
<link href="https://fonts.googleapis.com/css2?family=Comfortaa:wght@400&family=Open+Sans:wght@300;400&display=swap" rel="stylesheet">
<style>
  :root {
    --backdrop: #e7e4de;
    --card-dark: #0e0e0e;
    --card-mid: #1c1c1c;
    --brand-green: rgb(187, 207, 65);
    --silver: #b9b9b9;
    --text-light: #c9c9c9;
    --text-dim: #9a9a9a;
  }
  * { margin: 0; padding: 0; box-sizing: border-box; }
  html, body {
    width: 1200px;
    height: 1022px;
    overflow: hidden;
    background: var(--backdrop);
  }
  .card {
    position: absolute;
    left: 150px;
    top: 254px;
    width: 900px;
    height: 514px;
    border-radius: 6px;
    overflow: hidden;
    box-shadow: 0 18px 40px rgba(0, 0, 0, 0.35);
  }
  .card-texture {
    position: absolute;
    inset: 0;
    width: 100%;
    height: 100%;
    background: radial-gradient(ellipse at 35% 40%, var(--card-mid) 0%, var(--card-dark) 75%);
  }
  .brand {
    position: absolute;
    left: 60px;
    bottom: 70px;
    display: flex;
    align-items: center;
    gap: 16px;
  }
  .brand-mark {
    width: 78px;
    height: 78px;
    background: var(--brand-green);
  }
  .brand-text { display: flex; flex-direction: column; gap: 6px; }
  .brand-name {
    font-family: "Open Sans", sans-serif;
    font-weight: 400;
    font-size: 30px;
    color: var(--silver);
    letter-spacing: 0.5px;
  }
  .brand-slogan {
    font-family: "Open Sans", sans-serif;
    font-weight: 300;
    font-size: 15px;
    line-height: 1.3;
    color: var(--text-dim);
    letter-spacing: 1.5px;
  }
  .contact {
    position: absolute;
    right: 70px;
    top: 56px;
    width: 330px;
    font-family: "Open Sans", sans-serif;
    font-weight: 300;
    color: var(--text-light);
  }
  .contact-name {
    font-family: "Comfortaa", sans-serif;
    font-size: 30px;
    color: var(--brand-green);
    letter-spacing: 1px;
  }
  .contact-role {
    font-size: 17px;
    color: var(--text-dim);
    letter-spacing: 1.5px;
    margin: 4px 0 14px;
  }
  .contact-list { list-style: none; }
  .contact-item {
    display: flex;
    align-items: center;
    gap: 12px;
    font-size: 18px;
    letter-spacing: 1.5px;
    line-height: 30px;
  }
  .contact-icon { width: 16px; height: 16px; fill: var(--brand-green); flex: none; }
  .contact-address {
    margin-top: 20px;
    font-size: 18px;
    letter-spacing: 1.5px;
    line-height: 28px;
    color: var(--text-dim);
  }
</style>
</head>
<body>
  <section class="card">
    <svg class="card-texture" role="img" aria-label="Embossed ripple pattern of concentric circles on glossy black card stock" viewBox="0 0 900 514" preserveAspectRatio="none">
      <defs>
        <radialGradient id="cardGloss" cx="0.35" cy="0.4" r="0.8">
          <stop offset="0" stop-color="#1e1e1e"/>
          <stop offset="1" stop-color="#0c0c0c"/>
        </radialGradient>
      </defs>
      <rect width="900" height="514" fill="url(#cardGloss)"/>
    </svg>

    <div class="brand">
      <div class="brand-mark"></div>
      <div class="brand-text">
        <span class="brand-name">Ripplecraft Facades</span>
        <span class="brand-slogan">decorative panels for<br>interiors &amp; landscapes</span>
      </div>
    </div>

    <div class="contact">
      <h1 class="contact-name">Owen Calder</h1>
      <p class="contact-role">President</p>
      <ul class="contact-list">
        <li class="contact-item">
          <svg class="contact-icon" viewBox="0 0 16 16"><rect x="4" y="1" width="8" height="14" rx="1.5"/></svg>
          331. 480. 1926
        </li>
        <li class="contact-item">
          <svg class="contact-icon" viewBox="0 0 16 16"><path d="M3 1l3 3-1.5 2a9 9 0 0 0 5.5 5.5L12 10l3 3-2 2C7 15 1 9 1 3z"/></svg>
          331. 480. 1927
        </li>
        <li class="contact-item">
          <svg class="contact-icon" viewBox="0 0 16 16"><rect x="4" y="1" width="8" height="5"/><rect x="1" y="6" width="14" height="6" rx="1"/><rect x="4" y="11" width="8" height="4"/></svg>
          331. 480. 1928
        </li>
        <li class="contact-item">
          <svg class="contact-icon" viewBox="0 0 16 16"><path d="M1 3h14v10H1z M1 3l7 6 7-6" stroke="#0e0e0e" stroke-width="1"/></svg>
          owen@ripplecraft.com
        </li>
        <li class="contact-item">
          <svg class="contact-icon" viewBox="0 0 16 16"><circle cx="8" cy="8" r="7"/><path d="M1 8h14M8 1v14M3 4h10M3 12h10" stroke="#0e0e0e" stroke-width="1" fill="none"/></svg>
          www.ripplecraft.com
        </li>
      </ul>
      <p class="contact-address">42 Harbour Lane<br>Fernvale, NSW 2480</p>
    </div>
  </section>
</body>
</html>
```